Tolbek cards

I want a simple business card that pops.
Logo on one side.
On side two i want.
"Are you thinking about a new building on your property, or renovating an existing structure? Contact".....
Owners Name: Dale Whitacre
Owners Phone number: 610-555-0187
Address:4076 Copper Ridge RD, Alden Falls, PA 16850
Committed to Quality, Service, and Integrity

```html
<!DOCTYPE html>
<html lang="en">
<head>
<meta charset="utf-8">
<title>Tolbek Builders LLC – Business Card</title>
<link rel="stylesheet" href="https://fonts.googleapis.com/css2?family=Archivo:wght@400;500;700;800&display=swap">
<style>
  :root {
    --stage: #262626;
    --bronze-light: #9d8569;
    --bronze-dark: #563b28;
    --brown-deep: #4a3323;
    --tan: #a08a6c;
    --paper: #f3f2f0;
    --ink: #2e2219;
    --white: #ffffff;
  }
  * { margin: 0; padding: 0; box-sizing: border-box; }
  html, body {
    width: 1200px; height: 576px; overflow: hidden;
    background: var(--stage);
    font-family: "Archivo", Arial, sans-serif;
  }
  .canvas { position: relative; width: 1200px; height: 576px; }
  .card {
    position: absolute; top: 139px; width: 484px; height: 292px;
    border-radius: 10px; overflow: hidden;
  }
  p, div, span { line-height: 1; }

  /* Front */
  .card--front {
    left: 102px;
    background: linear-gradient(180deg, var(--bronze-light) 0%, #7d6349 55%, var(--bronze-dark) 100%);
  }
  .card--front .brand__square {
    position: absolute; left: 50%; top: 70px; width: 60px; height: 60px;
    transform: translateX(-50%); background: var(--paper); opacity: .9;
  }
  .card--front .brand__name,
  .card--front .brand__sub {
    position: absolute; left: 0; right: 0; text-align: center;
    font-weight: 800; text-transform: uppercase; color: var(--paper);
  }
  .card--front .brand__name { top: 153px; font-size: 48px; letter-spacing: 1px; }
  .card--front .brand__sub { top: 200px; font-size: 16px; letter-spacing: 1.5px; }
  .tagline {
    position: absolute; left: 0; right: 0; text-align: center;
    font-size: 13px; font-weight: 400;
  }
  .card--front .tagline { top: 256px; color: var(--white); }
  .rule { position: absolute; height: 1px; }
  .card--front .rule { top: 263px; width: 70px; background: linear-gradient(90deg, transparent, #e9e1d6); }
  .card--front .rule--left { left: 48px; }
  .card--front .rule--right { right: 48px; transform: scaleX(-1); }

  /* Back */
  .card--back { left: 596px; background: var(--paper); }
  .card--back .brand__square {
    position: absolute; left: 116px; top: 25px; width: 46px; height: 46px;
    background: var(--brown-deep);
  }
  .card--back .brand {
    position: absolute; top: 31px; left: 172px;
    font-weight: 800; text-transform: uppercase; color: var(--brown-deep);
  }
  .card--back .brand__name { display: block; font-size: 38px; letter-spacing: 1px; }
  .card--back .brand__sub { display: block; font-size: 13px; letter-spacing: 3.2px; margin-top: 2px; }
  .pitch {
    position: absolute; left: 0; right: 0; top: 101px; height: 54px;
    background: var(--brown-deep); color: var(--white);
    text-align: center; font-size: 13px; font-weight: 700;
    text-transform: uppercase; letter-spacing: .3px; line-height: 16px;
    padding-top: 8px;
  }
  .contact-pill {
    position: absolute; left: 50%; top: 146px; transform: translateX(-50%);
    width: 98px; height: 17px; border-radius: 9px;
    background: var(--tan); color: var(--white);
    font-size: 12px; font-weight: 700; text-transform: uppercase;
    text-align: center; line-height: 17px;
  }
  .owner {
    position: absolute; left: 0; right: 0; top: 173px; text-align: center;
    font-size: 20px; font-weight: 700; text-transform: uppercase; color: var(--ink);
  }
  .owner__last { color: var(--tan); }
  .phone {
    position: absolute; left: 0; right: 0; top: 199px; text-align: center;
    font-size: 13px; font-weight: 700; color: #111;
  }
  .address {
    position: absolute; left: 0; right: 0; top: 217px; text-align: center;
    font-size: 12px; color: var(--tan);
  }
  .card--back .rule { top: 244px; left: 42px; right: 42px; background: linear-gradient(90deg, transparent, #b9a78f 20%, #b9a78f 80%, transparent); }
  .card--back .tagline { top: 256px; color: var(--ink); }
</style>
</head>
<body>
<main class="canvas">
  <section class="card card--front" aria-label="Card front">
    <div class="brand__square"></div>
    <div class="brand__name">Tolbek</div>
    <div class="brand__sub">Builders LLC</div>
    <span class="rule rule--left"></span>
    <p class="tagline">Committed to Quality, Service &amp; Integrity</p>
    <span class="rule rule--right"></span>
  </section>

  <section class="card card--back" aria-label="Card back">
    <div class="brand__square"></div>
    <div class="brand">
      <span class="brand__name">Tolbek</span>
      <span class="brand__sub">Builders LLC</span>
    </div>
    <p class="pitch">Are you thinking about a new building on your<br>property, or renovating an existing structure?</p>
    <div class="contact-pill">Contact</div>
    <p class="owner">Dale <span class="owner__last">Whitacre</span></p>
    <p class="phone">Call: 610-555-0187</p>
    <p class="address">Add.: 4076 Copper Ridge RD, Alden Falls, PA 16850</p>
    <span class="rule"></span>
    <p class="tagline">Committed to Quality, Service &amp; Integrity</p>
  </section>
</main>
</body>
</html>
```